Frostvale Harborline LLC

we need a business card design

Industry/Entity Type

hvac

Contact Information for Business Card

my logo

Requirements
Must have
• my logo and same colors

```html
<!DOCTYPE html>
<html lang="en">
<head>
<meta charset="utf-8">
<title>Frostvale Harborline LLC – Business Card</title>
<link href="https://fonts.googleapis.com/css2?family=Montserrat:wght@400;500;700;800&display=swap" rel="stylesheet">
<style>
  :root {
    --card-blue: #1160a8;
    --accent-cyan: #1aa8e0;
    --accent-gold: #f9b847;
    --text-white: #ffffff;
    --backdrop: #2b2b2b;
  }
  * { box-sizing: border-box; margin: 0; padding: 0; }
  html, body { width: 1200px; height: 875px; overflow: hidden; }
  body {
    background: var(--backdrop);
    font-family: "Montserrat", Arial, sans-serif;
    display: flex;
    align-items: center;
    justify-content: center;
    gap: 40px;
  }
  .card {
    position: relative;
    width: 520px;
    height: 300px;
    background: var(--card-blue);
    border-radius: 18px;
    overflow: hidden;
    color: var(--text-white);
  }
  .card-band {
    position: absolute;
    left: 0; bottom: 0;
    width: 520px; height: 14px;
  }
  /* front */
  .front-brand {
    position: absolute;
    inset: 0 0 14px 0;
    display: flex;
    align-items: center;
    justify-content: center;
    gap: 12px;
  }
  .brand-mark {
    width: 22px; height: 22px;
    border-radius: 50%;
    background: var(--accent-gold);
    flex: none;
  }
  .brand-name {
    font-weight: 800;
    font-size: 24px;
    line-height: 1.15;
    color: var(--text-white);
    text-transform: uppercase;
    letter-spacing: 0.5px;
  }
  /* back */
  .back-brand {
    position: absolute;
    left: 70px; top: 62px;
    width: 200px;
    display: flex;
    align-items: center;
    gap: 10px;
  }
  .back-brand .brand-name { font-size: 17px; }
  .back-brand .brand-mark { width: 16px; height: 16px; }
  .divider {
    position: absolute;
    left: 290px; top: 60px;
    width: 1px; height: 100px;
    background: var(--accent-cyan);
  }
  .contact-list {
    position: absolute;
    left: 306px; top: 66px;
    list-style: none;
    font-size: 12.5px;
    font-weight: 500;
  }
  .contact-list li {
    display: flex;
    align-items: center;
    gap: 8px;
    margin-bottom: 10px;
  }
  .contact-list svg { width: 12px; height: 12px; flex: none; }
  .person {
    position: absolute;
    left: 70px; top: 168px;
  }
  .person-name {
    font-weight: 700;
    font-size: 24px;
    letter-spacing: 0.5px;
    text-transform: uppercase;
  }
  .person-name .first { color: var(--accent-cyan); }
  .person-name .last { color: var(--accent-gold); }
  .person-role {
    font-size: 13px;
    font-weight: 500;
    text-align: right;
  }
  .address {
    position: absolute;
    left: 70px; top: 240px;
    font-size: 13px;
    font-weight: 500;
  }
</style>
</head>
<body>

  <section class="card card-front">
    <div class="front-brand">
      <span class="brand-mark"></span>
      <span class="brand-name">Frostvale<br>Harborline LLC</span>
    </div>
    <svg class="card-band" viewBox="0 0 520 14" preserveAspectRatio="none">
      <rect x="0" y="6" width="520" height="8" fill="var(--accent-cyan)"/>
      <polygon points="300,6 306,0 520,0 520,14 292,14" fill="var(--accent-gold)"/>
    </svg>
  </section>

  <section class="card card-back">
    <div class="back-brand">
      <span class="brand-mark"></span>
      <span class="brand-name">Frostvale<br>Harborline LLC</span>
    </div>
    <div class="divider"></div>
    <ul class="contact-list">
      <li>
        <svg viewBox="0 0 24 24"><path fill="var(--accent-gold)" d="M6.6 10.8a15.1 15.1 0 0 0 6.6 6.6l2.2-2.2a1 1 0 0 1 1-.25 11.4 11.4 0 0 0 3.6.57 1 1 0 0 1 1 1V20a1 1 0 0 1-1 1A17 17 0 0 1 3 4a1 1 0 0 1 1-1h3.5a1 1 0 0 1 1 1c0 1.25.2 2.45.57 3.57a1 1 0 0 1-.25 1z"/></svg>
        303.555.0148
      </li>
      <li>
        <svg viewBox="0 0 24 24"><rect x="2" y="5" width="20" height="14" rx="1" fill="var(--accent-gold)"/><path d="M2 6l10 7 10-7" fill="none" stroke="var(--card-blue)" stroke-width="2"/></svg>
        info@frostvaleharbor.com
      </li>
      <li>
        <svg viewBox="0 0 24 24"><g fill="none" stroke="var(--accent-gold)" stroke-width="2"><circle cx="12" cy="12" r="9"/><ellipse cx="12" cy="12" rx="4" ry="9"/><path d="M3 12h18"/></g></svg>
        www.frostvaleharbor.com
      </li>
    </ul>
    <div class="person">
      <p class="person-name"><span class="first">Dana</span> <span class="last">Whitlock</span></p>
      <p class="person-role">Founder</p>
    </div>
    <p class="address">4/22 Harbor Crest Rd Eastbrook ABC 4120</p>
    <svg class="card-band" viewBox="0 0 520 14" preserveAspectRatio="none">
      <rect x="0" y="6" width="520" height="8" fill="var(--accent-cyan)"/>
      <polygon points="300,6 306,0 520,0 520,14 292,14" fill="var(--accent-gold)"/>
    </svg>
  </section>

</body>
</html>
```